" Temos uma food bike e trabalhamos com eventos e agora estamos passando por um processo de expansão para colocar os produtos nas prateleiras dos mercados. Viemos para o mercado com o intuito de apresentar esse tão tradicional produto, porém com uma nova vertente, mais delicioso e cremoso, podendo ser Tropical Premium (100% da fruta), Cremoso Premium e Premium (Recheados) - agradando assim a todo tipo de público. Não fazemos uso de corantes e aromatizantes. Utilizamos produtos de alta qualidade, podendo ser considerado como Gourmet. Temos um cuidado especial com a seleção de cada ingrediente e seguimos rigorosamente aos padrões de manipulação: cada Sacolé vem com uma embalagem externa, garantindo assim uma proteção a mais para o saquinho interno, que será diretamente levado a boca. "

```html
<!DOCTYPE html>
<html lang="pt-BR">
<head>
<meta charset="UTF-8">
<title>Doce Brisa – Embalagem Cremoso</title>
<link href="https://fonts.googleapis.com/css2?family=Anton&family=Oswald:wght@400;600;700&family=Dancing+Script:wght@700&display=swap" rel="stylesheet">
<style>
  :root{
    --page-bg:#eef1f4;
    --choc-dark:#2c1610;
    --choc:#3d2118;
    --choc-light:#5b3326;
    --berry:#7c1b1f;
    --berry-deep:#5a1216;
    --cream:#f3e6cc;
    --gold:#f2c230;
    --white:#ffffff;
    --board:#6b4328;
    --board-edge:#4a2c19;
  }
  *{margin:0;padding:0;box-sizing:border-box;}
  html,body{width:1200px;height:1200px;overflow:hidden;background:var(--page-bg);}
  .canvas{position:relative;width:1200px;height:1200px;}
  .pack{
    position:absolute;left:396px;top:12px;width:408px;height:1176px;
    background:var(--choc);overflow:hidden;
    box-shadow:0 6px 24px rgba(0,0,0,.25);
  }
  .pack > *{position:absolute;}

  /* top panel */
  .top-panel{left:0;top:0;width:408px;height:396px;
    background:linear-gradient(90deg,var(--choc-dark) 0%,var(--choc) 40%,var(--berry) 78%,var(--berry-deep) 100%);}
  .top-photo{left:150px;top:0;width:258px;height:170px;
    background:radial-gradient(ellipse at 70% 25%,var(--choc-light) 0%,rgba(61,33,24,.6) 40%,rgba(61,33,24,0) 72%);}
  .flavor-label{left:6px;top:30px;width:60px;height:180px;
    display:flex;align-items:center;justify-content:center;}
  .flavor-label span{display:block;transform:rotate(-90deg);white-space:nowrap;
    font-family:"Anton",sans-serif;font-size:40px;letter-spacing:1px;color:var(--cream);}
  .brand-band{left:40px;top:196px;width:368px;height:64px;
    background:linear-gradient(90deg,rgba(124,27,31,0),var(--berry) 25%,var(--berry) 85%,var(--berry-deep));}
  .brand{left:0;top:178px;width:408px;height:100px;
    display:flex;align-items:center;justify-content:center;gap:14px;}
  .brand-dot{width:64px;height:64px;border-radius:50%;background:var(--gold);flex:none;}
  .brand-name{font-family:"Oswald",sans-serif;font-weight:700;font-size:44px;color:var(--cream);white-space:nowrap;}
  .ingredient-photo{left:20px;top:298px;width:150px;height:90px;
    background:radial-gradient(ellipse at 45% 55%,#efe7da 0%,#b08866 35%,rgba(90,50,30,0) 70%);}

  /* transparent visor */
  .window{left:0;top:396px;width:408px;height:170px;
    background:
      linear-gradient(90deg,rgba(255,255,255,.12) 0,rgba(255,255,255,0) 18%,rgba(255,255,255,0) 82%,rgba(255,255,255,.12) 100%),
      linear-gradient(180deg,#2a1410,#4a1a1c 50%,#2a1410);
    border-top:2px solid rgba(255,255,255,.25);border-bottom:2px solid rgba(255,255,255,.25);}

  /* info */
  .info-panel{left:0;top:566px;width:408px;height:320px;
    background:linear-gradient(180deg,var(--choc-dark),var(--choc));}
  .tagline{left:0;top:618px;width:408px;text-align:center;
    font-family:"Dancing Script",cursive;font-size:26px;color:var(--cream);}
  .tagline::before,.tagline::after{content:"↑";font-family:"Oswald",sans-serif;font-size:18px;color:var(--gold);margin:0 10px;}
  .category{left:0;top:668px;width:408px;text-align:center;
    font-family:"Oswald",sans-serif;font-weight:400;font-size:20px;letter-spacing:2px;color:var(--cream);}
  .name-field{left:64px;top:718px;width:280px;height:56px;border-radius:28px;background:var(--white);}
  .subtitle{left:0;top:794px;width:408px;text-align:center;
    font-family:"Oswald",sans-serif;font-weight:700;font-size:27px;letter-spacing:1px;color:var(--cream);}

  /* bottom */
  .bottom-panel{left:0;top:860px;width:408px;height:316px;
    background:linear-gradient(180deg,var(--choc) 0%,var(--berry-deep) 55%,var(--choc-dark) 100%);}
  .sign{left:110px;top:884px;width:200px;height:112px;background:var(--board);
    border:3px solid var(--board-edge);border-radius:4px;transform:rotate(-4deg);
    display:flex;flex-direction:column;align-items:center;justify-content:center;}
  .sign span{font-family:"Anton",sans-serif;font-size:34px;line-height:1.05;color:var(--cream);}
  .food-photo{left:20px;top:1004px;width:368px;height:136px;border-radius:12px;
    background:radial-gradient(ellipse at 25% 40%,#6b3a22,transparent 60%),
               radial-gradient(ellipse at 72% 55%,#efe7da,transparent 42%),
               linear-gradient(90deg,#b4542a,#3a1d13);}
  .handle{left:0;top:1148px;width:408px;text-align:center;
    font-family:"Oswald",sans-serif;font-size:15px;letter-spacing:1px;color:var(--cream);}
</style>
</head>
<body>
<div class="canvas">
  <section class="pack">
    <div class="top-panel"></div>
    <div class="top-photo" role="img" aria-label="Pedaços de chocolate"></div>
    <div class="flavor-label"><span>CREMOSO</span></div>
    <div class="brand-band"></div>
    <div class="brand"><div class="brand-dot"></div><div class="brand-name">Doce Brisa</div></div>
    <div class="ingredient-photo" role="img" aria-label="Coco e chocolate"></div>
    <div class="window" role="img" aria-label="Viseira transparente mostrando o sacolé sabor chocolate"></div>
    <div class="info-panel"></div>
    <p class="tagline">Delicioso</p>
    <p class="category">- GELADINHO GOURMET -</p>
    <div class="name-field"></div>
    <p class="subtitle">SOBREMESA AFETIVA</p>
    <div class="bottom-panel"></div>
    <div class="sign"><span>MUITO</span><span>CREMOSO</span></div>
    <div class="food-photo" role="img" aria-label="Trufas de chocolate, coco e frutas"></div>
    <p class="handle">@DOCEBRISA</p>
  </section>
</div>
</body>
</html>
```